Dental Practice Website design

Design a new website for Brambleford Dental Practice.
Design should be warm, neutral in colour, with some small amount of bright colour if needed but kept to a minimum. Website should look professional, high end. Home page should be easy to navigate and simple for patients to be able to book online.
Logo in files along with some examples of websites that we like. Please ask if any further info needed.
Menu should have:
About
New Patients
Treatments
Fees
Contact Us

Industry/Entity Type

Dentistry

Number of Pages Required

4 page

Font styles to use
Sans Serif

Colors

Designer to choose colors to be used in the design.

Requirements
Must have
• Ravelle ratings badge, book online button,
Nice to have
• neutral, relaxing colours
Should not have
• harsh, bright colours!

```html
<!DOCTYPE html>
<html lang="en">
<head>
<meta charset="utf-8">
<title>Brambleford Dental Practice – Contact Us</title>
<link href="https://fonts.googleapis.com/css2?family=Montserrat:wght@300;400;600;700&family=Poppins:wght@300;400;500;600&display=swap" rel="stylesheet">
<style>
:root{
  --blue:#1283c8;
  --ink:#111111;
  --text:#222222;
  --muted:#6b6b6b;
  --line:#e4e4e4;
  --sand:#f4f3f1;
  --hero:#d3d3d3;
  --white:#ffffff;
  --black:#000000;
  --badge:#e7e7e7;
}
*{box-sizing:border-box;margin:0;padding:0}
html,body{width:1200px;height:2680px;overflow:hidden}
body{font-family:"Poppins",sans-serif;color:var(--text);background:var(--white);position:relative}
a{color:inherit;text-decoration:none}

/* top bar */
.topbar{position:absolute;left:0;top:0;width:1200px;height:54px;background:var(--sand)}
.topbar .contact{position:absolute;left:118px;top:16px;display:flex;gap:12px;align-items:center;font-size:12px;font-weight:500}
.topbar .contact span{display:flex;align-items:center;gap:7px}
.btn{display:inline-flex;align-items:center;justify-content:center;background:var(--blue);color:var(--white);font-weight:500;text-transform:uppercase}
.topbar .btn{position:absolute;left:862px;top:0;width:219px;height:54px;font-size:13.5px}

/* brand */
.brand{position:absolute;left:0;top:54px;width:1200px;height:154px;display:flex;flex-direction:column;align-items:center;justify-content:center}
.brand .mark{width:16px;height:16px;border:1.5px solid var(--text);margin-bottom:8px}
.brand .name{font-size:36px;font-weight:300;letter-spacing:1px;line-height:1;color:var(--text)}
.brand .sub{font-size:17px;font-weight:300;letter-spacing:1px;color:var(--text);margin-top:4px}

/* nav */
.nav{position:absolute;left:0;top:208px;width:1200px;height:66px;border-top:1px solid var(--line)}
.nav a{position:absolute;top:24px;transform:translateX(-50%);font-size:13.5px;font-weight:500;color:var(--ink);white-space:nowrap}
.nav a.active{color:var(--blue)}

/* hero */
.hero{position:absolute;left:0;top:274px;width:1200px;height:420px;background:var(--hero)}
.hero .skyline{position:absolute;left:0;bottom:0;width:1200px;height:300px;background:linear-gradient(180deg,rgba(211,211,211,0) 0%,rgba(170,170,170,.45) 100%)}
.hero h1{position:absolute;left:118px;top:88px;font-family:"Montserrat",sans-serif;font-size:60px;font-weight:700;color:var(--white);text-shadow:0 2px 4px rgba(0,0,0,.25)}
.hero p{position:absolute;left:120px;top:168px;width:820px;font-size:12px;line-height:18px;color:var(--ink)}
.hero .btn{position:absolute;left:119px;top:216px;width:188px;height:37px;font-size:13.5px}

.callband{position:absolute;left:0;top:694px;width:1200px;height:69px;background:var(--blue);color:var(--white);font-family:"Montserrat",sans-serif;font-weight:300;font-size:33px;display:flex;align-items:center;justify-content:center}

/* section heads */
.sechead{position:absolute;left:0;width:1200px;text-align:center}
.sechead .eyebrow{font-size:18px;color:var(--ink)}
.sechead h2{font-size:46px;font-weight:600;color:var(--ink);line-height:1.3;margin-top:2px}
.sechead h2 em{font-style:normal;color:var(--blue)}
.sechead p{font-size:17px;color:var(--ink);margin-top:2px}

/* form */
.formcard{position:absolute;left:118px;top:955px;width:965px;height:362px;border:1.5px solid var(--line);border-radius:22px;overflow:hidden;background:var(--white)}
.field{position:absolute;border:1px solid var(--line);border-radius:4px;font-size:12.5px;color:var(--muted);padding:12px 15px;background:var(--white)}
.sendbtn{position:absolute;left:44px;top:301px;width:176px;height:39px;border-radius:20px;background:var(--blue);color:var(--white);font-size:12.5px;font-weight:500;display:flex;align-items:center;padding-left:34px;gap:18px}
.sendbtn i{width:26px;height:26px;border-radius:50%;background:var(--white);display:flex;align-items:center;justify-content:center}
.team{position:absolute;left:540px;top:0;width:425px;height:362px;background:radial-gradient(ellipse 62% 70% at 55% 78%,#9fbde0 0%,#c7d8ec 38%,#eaf0f7 68%,rgba(255,255,255,0) 100%)}

/* info cards */
.card{position:absolute;top:1522px;width:212px;height:177px;border:1.5px solid var(--line);border-radius:18px;padding:22px 22px}
.card .ico{width:40px;height:40px;border-radius:50%;background:#e8f2fa;display:flex;align-items:center;justify-content:center}
.card h3{font-size:15.5px;font-weight:600;color:#123a5c;margin-top:14px}
.card p{font-size:14px;line-height:20px;color:var(--ink);margin-top:12px}
.card p.small{font-size:11.5px;line-height:18px}

.map{position:absolute;left:118px;top:1735px;width:965px;height:363px;border-radius:22px;border:1.5px solid var(--line);background:radial-gradient(ellipse 70% 60% at 45% 50%,#ececec 0%,#e4e4e4 55%,#d9d9d9 100%)}

.partners{position:absolute;top:2192px;height:40px;background:var(--badge);border-radius:6px}

/* footer */
.footer{position:absolute;left:0;top:2289px;width:1200px;height:329px;background:var(--sand)}
.fcol{position:absolute;top:50px}
.fcol h4{font-size:17.5px;font-weight:600;color:var(--ink);text-transform:uppercase;margin-bottom:22px}
.fcol li{list-style:none;font-size:14px;color:var(--ink);line-height:27.5px}
.fcontact li{display:flex;align-items:center;gap:12px;font-size:15px;line-height:37px}
.follow{display:flex;align-items:center;gap:6px;font-size:13.5px;margin-top:8px}
.follow .s{width:30px;height:30px;border-radius:50%;background:var(--black)}
.badges{position:absolute;left:119px;top:261px;display:flex;gap:17px;align-items:center}
.badges .b{height:48px;background:#e3e3e3;border-radius:3px}
.badges .ravelle{font-size:20px;font-weight:600;color:var(--blue);margin-left:6px}
.hours{position:absolute;left:797px;top:0;width:285px;height:329px;background:var(--blue);color:var(--white);padding:46px 30px}
.hours h4{font-size:17.5px;font-weight:600;margin-bottom:16px}
.hours li{list-style:none;font-size:15.5px;line-height:33.4px}

.copyright{position:absolute;left:0;top:2618px;width:1200px;height:62px;background:var(--black);color:var(--white);font-size:12px;font-weight:500;display:flex;align-items:center;justify-content:center;text-transform:uppercase}
</style>
</head>
<body>

<header class="topbar">
  <div class="contact">
    <span><svg width="18" height="18" viewBox="0 0 24 24" fill="none" stroke="#222" stroke-width="1.5"><path d="M5 3h4l2 5-2.5 1.5a11 11 0 0 0 6 6L16 13l5 2v4a2 2 0 0 1-2 2A17 17 0 0 1 3 5a2 2 0 0 1 2-2z"/></svg>+44 (161) 555-0142</span>
    <span><svg width="18" height="14" viewBox="0 0 24 18" fill="none" stroke="#222" stroke-width="1.5"><rect x="1" y="1" width="22" height="16"/><path d="M1 1l11 9 11-9"/></svg>info@bramblefordental.com</span>
  </div>
  <a class="btn" href="#">Book an Appointment</a>
</header>

<div class="brand">
  <div class="mark"></div>
  <div class="name">BRAMBLEFORD</div>
  <div class="sub">DENTAL PRACTICE</div>
</div>

<nav class="nav">
  <a class="active" style="left:223px" href="#">HOME</a>
  <a style="left:346px" href="#">ABOUT US</a>
  <a style="left:497px" href="#">NEW PATIENTS</a>
  <a style="left:655px" href="#">TREATMENTS</a>
  <a style="left:790px" href="#">FEES</a>
  <a style="left:929px" href="#">CONTACT US</a>
</nav>

<section class="hero">
  <div class="skyline" role="img" aria-label="Line illustration of a city skyline with bridge, clock tower and observation wheel"></div>
  <h1>Contact Us</h1>
  <p>Lorem Ipsum is simply dummy text of the printing and typesetting industry. Lorem Ipsum has been the industry's standard dummy text ever since the 1500s, when an unknown printer took.</p>
  <a class="btn" href="#">Book an Appointment</a>
</section>

<div class="callband">Get in touch with us today +44 (161) 555-0142</div>

<div class="sechead" style="top:802px">
  <div class="eyebrow">CONTACT US</div>
  <h2><em>Get</em> In Touch With Us</h2>
  <p>Lorem Ipsum is simply dummy text of the printing.</p>
</div>

<form class="formcard">
  <div class="team" role="img" aria-label="Photo of a male dentist in a white coat and a female dental nurse in blue scrubs, arms crossed"></div>
  <div class="field" style="left:49px;top:42px;width:212px;height:43px">Enter Name</div>
  <div class="field" style="left:284px;top:42px;width:212px;height:43px">Enter Email</div>
  <div class="field" style="left:49px;top:104px;width:212px;height:43px">Phone Number</div>
  <div class="field" style="left:284px;top:104px;width:212px;height:43px">Subject</div>
  <div class="field" style="left:49px;top:165px;width:447px;height:116px">Your Message</div>
  <div class="sendbtn">Send Message <i><svg width="14" height="10" viewBox="0 0 14 10" fill="none" stroke="#1283c8" stroke-width="1.8"><path d="M0 5h12M8 1l4 4-4 4"/></svg></i></div>
</form>

<div class="sechead" style="top:1356px">
  <div class="eyebrow">CONTACT INFO</div>
  <h2><em>Connecting</em> Near &amp; Far</h2>
  <p>Lorem Ipsum is simply dummy text of the printing.</p>
</div>

<div class="card" style="left:119px">
  <div class="ico"><svg width="20" height="20" viewBox="0 0 24 24" fill="none" stroke="#1283c8" stroke-width="1.4"><path d="M5 3h4l2 5-2.5 1.5a11 11 0 0 0 6 6L16 13l5 2v4a2 2 0 0 1-2 2A17 17 0 0 1 3 5a2 2 0 0 1 2-2z"/></svg></div>
  <h3>Contact Us</h3>
  <p>+44 (161) 555-0142<br>+44 (161) 555-0142</p>
</div>
<div class="card" style="left:367px">
  <div class="ico"><svg width="20" height="16" viewBox="0 0 24 18" fill="none" stroke="#1283c8" stroke-width="1.4"><rect x="1" y="1" width="22" height="16"/><path d="M1 1l11 9 11-9"/></svg></div>
  <h3>Email Us</h3>
  <p>info@domain.com<br>sales@domain.com</p>
</div>
<div class="card" style="left:614px">
  <div class="ico"><svg width="20" height="20" viewBox="0 0 24 24" fill="none" stroke="#1283c8" stroke-width="1.4"><circle cx="12" cy="12" r="10"/><path d="M12 6v6l4 2"/></svg></div>
  <h3>Working Hours</h3>
  <p>Mon to Sat<br>9:00AM to 9:00PM</p>
</div>
<div class="card" style="left:869px">
  <div class="ico"><svg width="18" height="20" viewBox="0 0 20 24" fill="none" stroke="#1283c8" stroke-width="1.4"><path d="M10 23s8-8 8-14a8 8 0 0 0-16 0c0 6 8 14 8 14z"/><circle cx="10" cy="9" r="3"/></svg></div>
  <h3>Visit Us On</h3>
  <p class="small">Lorem Ipsum is simply dummy text of the printing and.</p>
</div>

<div class="map" role="img" aria-label="Greyscale street map showing the practice area"></div>

<div class="partners" style="left:127px;width:115px"></div>
<div class="partners" style="left:292px;width:132px"></div>
<div class="partners" style="left:470px;width:119px"></div>
<div class="partners" style="left:635px;width:134px"></div>
<div class="partners" style="left:825px;width:98px"></div>
<div class="partners" style="left:958px;width:115px"></div>

<footer class="footer">
  <div class="fcol" style="left:119px">
    <h4>Quick Links</h4>
    <ul><li>About</li><li>New Patients</li><li>Treatments</li><li>Fees</li><li>Contact Us</li></ul>
  </div>
  <div class="fcol" style="left:293px">
    <h4>Dental Departments</h4>
    <ul><li>Cosmetic Dentistry</li><li>Endodontics</li><li>Oral Surgery</li><li>General Dental Care</li><li>Pediatric Dentistry</li></ul>
  </div>
  <div class="fcol fcontact" style="left:538px">
    <h4 style="margin-bottom:10px">Contact Us</h4>
    <ul>
      <li><svg width="22" height="22" viewBox="0 0 24 24" fill="none" stroke="#222" stroke-width="1.4"><path d="M5 3h4l2 5-2.5 1.5a11 11 0 0 0 6 6L16 13l5 2v4a2 2 0 0 1-2 2A17 17 0 0 1 3 5a2 2 0 0 1 2-2z"/></svg>+44 (161) 555-0142</li>
      <li><svg width="24" height="18" viewBox="0 0 24 18" fill="none" stroke="#222" stroke-width="1.4"><rect x="1" y="1" width="22" height="16"/><path d="M1 1l11 9 11-9"/></svg>info@bramblefordental.com</li>
      <li style="font-size:13.5px"><svg width="22" height="24" viewBox="0 0 20 24" fill="none" stroke="#222" stroke-width="1.4"><path d="M10 23s8-8 8-14a8 8 0 0 0-16 0c0 6 8 14 8 14z"/><circle cx="10" cy="9" r="3"/></svg>12 Fenwick Lane, UK</li>
    </ul>
    <div class="follow">Follow me:&nbsp;&nbsp;<span class="s"></span><span class="s"></span><span class="s"></span><span class="s"></span></div>
  </div>
  <div class="badges">
    <div class="b" style="width:92px"></div>
    <div class="b" style="width:91px"></div>
    <div class="b" style="width:92px"></div>
    <div class="ravelle">Ravelle Ratings</div>
  </div>
  <div class="hours">
    <h4>OPENING HOURS</h4>
    <ul>
      <li>Monday : 08.00 - 10.00</li>
      <li>Tuesday : 08.00 - 10.00</li>
      <li>Wednesday : 08.00 - 10.00</li>
      <li>Thursday : 08.00 - 10.00</li>
      <li>Friday : 09.00 - 07.00</li>
      <li>Saturday : 10.00 - 05.00</li>
      <li>Sunday : 10.00 - 05.00</li>
    </ul>
  </div>
</footer>

<div class="copyright">Copyright © 2025 Brambleford Dental Practice. All rights reserved.</div>

</body>
</html>
```